The 22 Rules and Traps of House Lending or the 22 things that will derail your transaction and how to prevent them.

I am looking to do a series of 4 to 5 e-books that should have a consistent format and theme

The first of these should be entitled, "The 22 Rules and Traps of House Lending" That is similar in style to the attached e-book.
The attached e-book is pretty much the style that I am looking for, The same format can be followed. I have attached a black and white head shot image for the head shot areas that appears on page two of the attached e-book. I have also attached my company logo.
Please feel free to use the same or similar colors in my logo for the lay-out of the e-book. However please do not feel limited to those colors. - Feel free to use your imagination.

The content can be found here.

http://www.fredtheloanfox.example/loan-advice.php

For the final “About” page of the e-book - Please entitle it… About Fred the Loan Fox.
The content for the last page can be found in the attached document - Owen Thistlewood bio2

The first page is where the creativity come in

Requirements
Must have
• Note that this project is for one e-book - However, once the designer and format is chosen the remainder of the projects will be launched

```html
<!DOCTYPE html>
<html lang="en">
<head>
<meta charset="utf-8">
<title>The 22 Rules and Traps of House Lending – Page 6</title>
<link href="https://fonts.googleapis.com/css2?family=Jost:wght@300;400;500;600;700&family=Cormorant+SC:wght@600;700&display=swap" rel="stylesheet">
<style>
  :root {
    --navy: #1f2a4f;
    --badge: #2c4a8c;
    --accent: #3f5fae;
    --alert: #e8322a;
    --body: #2b2f3a;
    --paper: #ffffff;
  }
  * { margin: 0; padding: 0; box-sizing: border-box; }
  html, body { width: 900px; height: 1200px; overflow: hidden; background: var(--paper); }
  .page {
    position: relative;
    width: 900px;
    height: 1200px;
    font-family: "Jost", sans-serif;
    color: var(--body);
  }
  .tip { position: absolute; left: 62px; width: 780px; }
  .tip-number {
    position: absolute;
    left: -42px;
    top: -6px;
    width: 50px;
    height: 50px;
    border-radius: 50%;
    background: var(--badge);
    color: #fff;
    font-family: "Cormorant SC", serif;
    font-weight: 700;
    font-size: 27px;
    line-height: 48px;
    text-align: center;
  }
  .tip-title {
    font-weight: 400;
    font-size: 27.5px;
    line-height: 34px;
    color: var(--navy);
    text-indent: 44px;
    margin-bottom: 14px;
  }
  .tip-title .verb { font-weight: 700; color: var(--accent); }
  .tip-title .verb.negative { color: var(--alert); }
  .tip-body {
    font-weight: 300;
    font-size: 15.4px;
    line-height: 21px;
    color: var(--body);
    margin-bottom: 14px;
  }
  .tip-body + .tip-body { margin-top: -4px; }
  .tip-rule {
    font-weight: 600;
    font-size: 17.6px;
    line-height: 29px;
    color: var(--accent);
  }
  .tip-10 { top: 60px; }
  .tip-11 { top: 372px; }
  .tip-12 { top: 812px; }

  .page-footer {
    position: absolute;
    left: 62px;
    right: 58px;
    top: 1108px;
    height: 40px;
    display: flex;
    align-items: center;
  }
  .brand {
    display: flex;
    align-items: center;
    gap: 8px;
    padding-right: 12px;
    border-right: 2px solid var(--navy);
    height: 34px;
  }
  .brand-mark { width: 14px; height: 14px; background: var(--navy); }
  .brand-name {
    font-family: "Cormorant SC", serif;
    font-weight: 700;
    font-size: 22px;
    color: var(--navy);
  }
  .series-title {
    margin-left: 14px;
    font-family: "Cormorant SC", serif;
    font-weight: 600;
    font-size: 17px;
    color: var(--navy);
  }
  .licence {
    margin-left: 60px;
    font-family: "Cormorant SC", serif;
    font-weight: 600;
    font-size: 17px;
    color: var(--navy);
  }
  .page-number {
    margin-left: auto;
    width: 30px;
    height: 30px;
    background: var(--navy);
    color: #fff;
    font-family: "Jost", sans-serif;
    font-size: 17px;
    line-height: 30px;
    text-align: center;
  }
</style>
</head>
<body>
<main class="page">

  <section class="tip tip-10">
    <span class="tip-number">10</span>
    <h2 class="tip-title"><span class="verb">Do</span> keep track of all bank statements and pay-stubs that come in during the un-derwriting process.</h2>
    <p class="tip-body">The underwriting process is not always predictable or logical. It is not always a smooth progression from loan submission to closing. More often than not, an underwriter may ask for additional pay stubs or bank statements, even though you have provided similar paperwork earlier in the underwriting process.</p>
    <p class="tip-rule">As a rule, avoid discarding any paperwork that is pertinent to the processing of your loan, especially pay-stubs and bank statements, until your transaction is closed. If you have a question as to whether a certain piece of paperwork is per-tinent to your transaction, simply ask your mortgage professional.</p>
  </section>

  <section class="tip tip-11">
    <span class="tip-number">11</span>
    <h2 class="tip-title"><span class="verb">Do</span> remember to cancel all automatic payments or auto drafts for mortgages and other debts while completing a refinance transaction.</h2>
    <p class="tip-body">One of the most overlooked tasks a borrower forgets is to cancel their automatic payments or auto drafts for mortgages and other debts that they have paid off as a part of their refinance transaction.<br>If a borrower forgets to cancel the automatic payments with former creditors it is likely that the former creditor will continue to debit the borrowers accounts, even thought the accounts have been paid off.</p>
    <p class="tip-body">Depending on the former creditor, it can be a struggle to get those erroneous payments refunded. To keep all of your accounts straight, it is best to remember to cancel your auto payments two weeks before the refinance is scheduled to close.</p>
    <p class="tip-rule">To be on the safe side, if you are paying off mortgages or debts as part of a re-finance with auto payments, you should contact your creditors and ask them what they recommend as the best method to cancel those auto-payments so your accounts are not debited incorrectly.</p>
  </section>

  <section class="tip tip-12">
    <span class="tip-number">12</span>
    <h2 class="tip-title"><span class="verb negative">Don’t</span> spend funds you would have normally used for a down-payment or clos-ing costs.</h2>
    <p class="tip-body">Emergencies do come up and in some rare cases money that was earmarked for a down-payment or for closing costs must be used for an emergency. If an emergency does happen, let your mortgage professional know immediately so alternate strategies can be devised to keep your transaction on track.</p>
    <p class="tip-rule">Loan approvals are based upon a specific set of circumstances, and if any of those circumstances change then the loan has to be re-underwritten and your loan could be delayed or worse denied. When in doubt, it is best to err on the side of communication with your mortgage professional.</p>
  </section>

  <footer class="page-footer">
    <div class="brand">
      <span class="brand-mark"></span>
      <span class="brand-name">Harborline</span>
    </div>
    <span class="series-title">The 22 Rules and Traps of House Lending</span>
    <span class="licence">Licence MLO#40872</span>
    <span class="page-number">6</span>
  </footer>

</main>
</body>
</html>
```